Shopping centre customer engagement software website

We need a multi page site with :

*What we do.
*How it works.
*Benefits
* Case study
* Testimonial
* Business login (we provide link to business portal)
* Consumer login (we provide link to consumer site)
* Book a demo
* Contact us

We want it to be clean and crisp and very self explanatory with little clutter. We are thinking white but are open to what ever looks the best.
Updates

Wordpress is preferred

Need extra days to review

Target Market(s)

Shopping centre managers and retail property companies

Coding

Coded - Design and coding required

Number of Pages Required

5+ page

Font styles to use
Sans Serif

Colors
ffffff

Requirements
Must have
• As listed above and must be responsive! Checkout our existing site for the text to be included (will be edited but it’ll give you an idea) www.vostrelink.com

```html
<!DOCTYPE html>
<html lang="en">
<head>
<meta charset="utf-8">
<title>Vostrelink – Shopping Centre Engagement</title>
<link rel="stylesheet" href="https://fonts.googleapis.com/css2?family=Montserrat:wght@400;500;600;700&family=PT+Sans:wght@400;700&display=swap">
<style>
:root{
  --blue:#3f82f5;
  --ink:#222;
  --text:#555;
  --muted:#888;
  --line:#e4e4e4;
  --grey-bg:#f3f3f3;
  --placeholder-a:#e4e5e8;
  --placeholder-b:#d3d5da;
  --footer:#333;
  --white:#fff;
}
*{box-sizing:border-box;margin:0;padding:0}
html,body{width:1200px;height:3774px;overflow:hidden}
body{font-family:"PT Sans",Arial,sans-serif;color:var(--text);background:var(--white);position:relative}
.heading{font-family:"Montserrat",Arial,sans-serif}
.btn{display:inline-block;background:var(--blue);color:var(--white);font-family:"Montserrat",Arial,sans-serif;font-weight:600;font-size:15px;letter-spacing:.5px;text-transform:uppercase;padding:0 30px;line-height:44px;border-radius:2px}
.rule{width:50px;height:2px;background:var(--muted);margin:22px auto 0}

/* nav */
.site-nav{position:absolute;top:0;left:0;width:1200px;height:60px;background:var(--white);z-index:3}
.nav-links{position:absolute;right:70px;top:0;display:flex;gap:34px;line-height:60px;font-family:"Montserrat",Arial,sans-serif;font-weight:600;font-size:14px;color:var(--ink)}
.brand{position:absolute;left:108px;top:4px;width:130px;height:110px;background:var(--white);border-radius:0 0 65px 65px;z-index:4;text-align:center}
.brand-dot{width:58px;height:58px;border-radius:50%;background:#b9bcc2;margin:8px auto 6px}
.brand-name{font-family:"Montserrat",Arial,sans-serif;font-weight:600;font-size:17px;color:#444}

/* hero */
.hero{position:absolute;top:60px;left:0;width:1200px;height:572px;background:linear-gradient(180deg,#7d7a70 0%,#a39c8d 40%,#6b6257 100%)}
.hero-shade{position:absolute;inset:0;background:rgba(20,20,20,.28)}
.hero-title{position:absolute;top:175px;left:0;width:100%;text-align:center;color:var(--white);font-weight:700;font-size:31px;line-height:38px}
.hero .btn{position:absolute;top:322px;left:520px;width:160px;text-align:center;padding:0}
.hero-dots{position:absolute;top:498px;left:0;width:100%;display:flex;justify-content:center;gap:12px}
.hero-dots span{width:9px;height:9px;border-radius:50%;background:rgba(255,255,255,.6)}
.hero-dots span.on{background:var(--white)}

/* benefits */
.benefits{position:absolute;top:632px;left:0;width:1200px;height:656px}
.section-title{text-align:center;font-weight:600;font-size:20px;color:var(--ink)}
.benefits .section-title{margin-top:54px}
.benefit-grid{position:absolute;top:143px;left:113px;width:970px;display:grid;grid-template-columns:repeat(4,1fr)}
.benefit{height:287px;padding:0 34px;text-align:center;border-right:1px solid var(--line);font-size:11.5px;line-height:15.5px;color:var(--text)}
.benefit:nth-child(4n){border-right:none}
.benefit:nth-child(n+5){height:172px;border-top:1px solid var(--line);padding-top:30px}
.benefit svg{display:block;margin:0 auto 36px;width:58px;height:58px}
.benefit:nth-child(n+5) svg{margin-bottom:28px;width:50px;height:50px}

/* what we do */
.what{position:absolute;top:1288px;left:0;width:1200px;height:423px;background:var(--grey-bg)}
.what-copy{position:absolute;left:133px;top:55px;width:500px;font-size:12.5px;line-height:18px}
.what-copy h2{font-weight:600;font-size:19px;color:var(--ink)}
.what-copy .rule{margin:14px 0 32px}
.what-copy p{margin-bottom:16px}
.what-copy .btn{margin-top:10px;font-size:13px;line-height:38px;padding:0 18px}
.what-divider{position:absolute;left:652px;top:55px;width:1px;height:310px;background:var(--line)}
.what-art{position:absolute;left:720px;top:60px;width:320px;height:300px;background:linear-gradient(160deg,var(--placeholder-a) 0%,var(--placeholder-b) 100%)}

/* photo band */
.band{position:absolute;top:1711px;left:0;width:1200px;height:314px;background:linear-gradient(180deg,#5a4a3e 0%,#7a6a58 50%,#3c3a3a 100%)}
.band-shade{position:absolute;inset:0;background:rgba(20,20,30,.35)}
.band-text{position:absolute;top:103px;left:320px;width:560px;text-align:center;color:var(--white);font-size:18px;line-height:28px}
.band-rule{position:absolute;top:200px;left:575px;margin:0;background:var(--white)}

/* how it works */
.how{position:absolute;top:2025px;left:0;width:1200px;height:415px;background:var(--blue)}
.how .section-title{color:var(--white);margin-top:44px;font-weight:500}
.how .rule{background:rgba(255,255,255,.7);margin-top:14px}
.steps{position:absolute;top:142px;left:118px;width:964px;display:flex;justify-content:space-between}
.step{width:160px;text-align:center;color:var(--white);font-family:"Montserrat",Arial,sans-serif}
.step-ring{width:126px;height:126px;border:3px solid var(--white);border-radius:50%;margin:0 auto;display:flex;align-items:center;justify-content:center}
.step-ring svg{width:54px;height:54px}
.step-num{font-size:19px;margin-top:20px}
.step-label{font-size:15px;font-weight:500;margin-top:6px}

/* case study */
.case{position:absolute;top:2440px;left:0;width:1200px;height:592px}
.case .section-title{margin-top:60px}
.case-sub{text-align:center;font-size:17px;color:var(--text);margin-top:6px}
.case .rule{margin-top:18px}
.stats{position:absolute;top:178px;left:226px;width:750px;display:grid;grid-template-columns:repeat(3,1fr);gap:30px 22px}
.stat{height:150px;background:var(--white);box-shadow:0 4px 16px rgba(0,0,0,.12);text-align:center;padding-top:46px}
.stat-value{font-family:"Montserrat",Arial,sans-serif;font-size:25px;color:var(--blue);font-weight:500}
.stat-label{font-size:14px;color:var(--ink);margin-top:12px}

/* closing band */
.closing{position:absolute;top:3032px;left:0;width:1200px;height:370px;background:linear-gradient(120deg,#6f9ef3 0%,#3f7ae6 55%,#2b5fc4 100%)}
.closing-text{position:absolute;top:122px;left:255px;width:690px;text-align:center;color:var(--white);font-weight:600;font-size:19px;line-height:28px}

/* footer */
.footer{position:absolute;top:3402px;left:0;width:1200px;height:372px;background:var(--footer);color:#ddd;font-size:11.5px}
.footer-brand{position:absolute;left:135px;top:70px;display:flex;align-items:center;gap:10px}
.footer-brand .brand-dot{width:22px;height:22px;margin:0;background:#9ea2a8}
.footer-brand .brand-name{color:#e6e6e6;font-size:20px}
.footer h4{font-family:"Montserrat",Arial,sans-serif;font-size:12px;font-weight:700;color:var(--white);letter-spacing:.5px;margin-bottom:16px}
.footer-contact{position:absolute;left:413px;top:52px}
.contact-row{display:flex;gap:12px;margin-bottom:16px;line-height:16px}
.contact-row svg{width:13px;height:13px;flex:none;margin-top:2px}
.footer-menu{position:absolute;left:665px;top:52px;line-height:17px}
.footer-news{position:absolute;left:860px;top:52px}
.news-input{width:210px;height:40px;background:var(--white);color:var(--muted);padding-left:12px;line-height:40px;font-size:11px}
.news-btn{display:inline-block;margin-top:16px;background:var(--blue);color:var(--white);font-family:"Montserrat",Arial,sans-serif;font-weight:700;font-size:11px;padding:0 14px;line-height:28px}
.footer-line{position:absolute;left:133px;right:133px;top:258px;height:1px;background:#4b4b4b}
.follow{position:absolute;left:133px;top:293px;display:flex;align-items:center;gap:8px}
.follow h4{margin:0 14px 0 0}
.social{width:26px;height:26px;border-radius:50%;background:var(--blue)}
.copyright{position:absolute;right:133px;top:300px;font-size:11px}
</style>
</head>
<body>

<header class="site-nav">
  <nav class="nav-links">
    <span>What we do</span><span>Benefits</span><span>Testimonials</span><span>How it works</span><span>Case study</span><span>Contact</span>
  </nav>
</header>
<div class="brand"><div class="brand-dot"></div><div class="brand-name">Vostrelink</div></div>

<section class="hero" role="img" aria-label="Photo of a busy multi-level shopping centre with escalators and shoppers">
  <div class="hero-shade"></div>
  <h1 class="hero-title heading">Vostrelink exceeds all expectations for<br>Shopping Centre Managers, Shoppers,<br>Tenants and Landlords</h1>
  <span class="btn">Read more</span>
  <div class="hero-dots"><span></span><span></span><span class="on"></span><span></span><span></span></div>
</section>

<section class="benefits">
  <h2 class="section-title heading">The benefits provided by Vostrelink</h2>
  <div class="rule"></div>
  <div class="benefit-grid">
    <div class="benefit">
      <svg viewBox="0 0 60 60" fill="none" stroke="#3f82f5" stroke-width="3"><path d="M14 4h24l10 10v42H14z" fill="#3f82f5"/><path d="M21 22h20M21 30h20M21 38h20M21 46h14" stroke="#fff"/></svg>
      Increase dwell times by setting triggers which send text messages rewarding loyalty E.g. If a shopper has been in the centre for an hour or more, an automatic text will be sent giving the shopper a reward such as free park or a free coffee.
    </div>
    <div class="benefit">
      <svg viewBox="0 0 60 60" fill="none" stroke="#3f82f5" stroke-width="4"><rect x="8" y="8" width="44" height="44" rx="3"/><path d="M30 40V18M21 27l9-9 9 9"/></svg>
      Provide undisputable proof to your tenants of marketing R.O.I E.g. You can provide metrics that prove out of the 1,000 targeted messages sent to their customers, within the past week, 350 stopped and entered their store. You can show them who their best customers were, how long they stayed in their stores and where they came from etc.
    </div>
    <div class="benefit">
      <svg viewBox="0 0 60 60" fill="#3f82f5"><path d="M6 24h10l22-12v36L16 36H6z"/><path d="M14 36l4 14h7l-3-14z"/><path d="M44 22q5 8 0 16M49 17q9 13 0 26" fill="none" stroke="#3f82f5" stroke-width="3"/></svg>
      Lower marketing costs by only directly marketing (text message) to your tenants ideal customer segment while they are shopping near their store.
    </div>
    <div class="benefit">
      <svg viewBox="0 0 60 60" fill="none" stroke="#3f82f5" stroke-width="3"><path d="M8 6v46h46"/><path d="M14 42l12-16 10 8 14-18"/><circle cx="26" cy="26" r="2.5" fill="#3f82f5"/><circle cx="36" cy="34" r="2.5" fill="#3f82f5"/></svg>
      Increase and measure customer loyalty through tailored targeted rewards and analytics.
    </div>
    <div class="benefit">
      <svg viewBox="0 0 52 52" fill="#3f82f5"><path d="M22 4h8l1 6 5 2 5-4 6 6-4 5 2 5 6 1v8l-6 1-2 5 4 5-6 6-5-4-5 2-1 6h-8l-1-6-5-2-5 4-6-6 4-5-2-5-6-1v-8l6-1 2-5-4-5 6-6 5 4 5-2z"/><circle cx="26" cy="26" r="8" fill="#fff"/></svg>
      Easy to install,<br>no wiring required.
    </div>
    <div class="benefit">
      <svg viewBox="0 0 52 52" fill="none" stroke="#3f82f5" stroke-width="4"><path d="M8 38a20 20 0 1 1 36 0"/><path d="M26 30l10-12"/><circle cx="26" cy="31" r="3" fill="#3f82f5"/></svg>
      Easy to use dashboard with<br>one click reporting.
    </div>
    <div class="benefit">
      <svg viewBox="0 0 52 52" fill="#3f82f5"><circle cx="26" cy="15" r="7"/><circle cx="11" cy="20" r="5"/><circle cx="41" cy="20" r="5"/><path d="M14 42a12 12 0 0 1 24 0z"/><path d="M2 40a9 9 0 0 1 14-7l-2 7zM50 40a9 9 0 0 0-14-7l2 7z"/></svg>
      Know who your customers are<br>personally and when they visit you.
    </div>
    <div class="benefit">
      <svg viewBox="0 0 52 52" fill="none" stroke="#3f82f5" stroke-width="3"><rect x="5" y="6" width="42" height="30" rx="2"/><path d="M20 44h12M26 36v8"/><path d="M16 30v-8M24 30V16M32 30v-6M38 30V13" stroke-width="4"/></svg>
      Have the data to back up<br>any decisions you make.
    </div>
  </div>
</section>

<section class="what">
  <div class="what-copy">
    <h2 class="heading">What we can do for you</h2>
    <div class="rule"></div>
    <p>Vostrelink provides shopping centre managers with an easy to use platform which enables them to delight their shoppers, impress their tenants, provide detailed data to their landlords and all accessible to them at the click of button.</p>
    <p>Vostrelink gives shopping centres real time tracking through smart IOTs of individual customer journeys through their physical stores, enabling highly targeted, relevant and timely promotional and rewarding capabilities. Furthermore, through deep analytical data processing of the customer journey, centre managers will be able to more accurately and reliably predict shopping behaviours.</p>
    <span class="btn">Read more</span>
  </div>
  <div class="what-divider"></div>
  <div class="what-art" role="img" aria-label="Product illustration area"></div>
</section>

<section class="band" role="img" aria-label="Photo of a wide shopping centre atrium with shoppers">
  <div class="band-shade"></div>
  <p class="band-text heading">Vostrelink is the ultimate marketing machine that can help you tailor to each individual and give you insights to do much more for your customers.</p>
  <div class="rule band-rule"></div>
</section>

<section class="how">
  <h2 class="section-title heading">How it Works</h2>
  <div class="rule"></div>
  <div class="steps">
    <div class="step">
      <div class="step-ring"><svg viewBox="0 0 54 54" fill="none" stroke="#fff" stroke-width="3"><rect x="5" y="12" width="44" height="30" rx="3"/><path d="M5 21h44" stroke-width="5"/><path d="M11 34h12"/></svg></div>
      <div class="step-num">01</div><div class="step-label">Allocate Cards</div>
    </div>
    <div class="step">
      <div class="step-ring"><svg viewBox="0 0 54 54" fill="none" stroke="#fff" stroke-width="3"><rect x="6" y="8" width="42" height="28"/><path d="M14 30l8-8 6 5 10-11"/><path d="M27 36v8M18 48l9-6 9 6"/></svg></div>
      <div class="step-num">02</div><div class="step-label">Direct Marketing</div>
    </div>
    <div class="step">
      <div class="step-ring"><svg viewBox="0 0 54 54" fill="none" stroke="#fff" stroke-width="3"><circle cx="27" cy="22" r="14"/><path d="M27 14l3 6 6 1-4 4 1 6-6-3-6 3 1-6-4-4 6-1z" fill="#fff" stroke="none"/><path d="M18 33l-4 15 7-3 4 6 2-9M36 33l4 15-7-3-4 6-2-9"/></svg></div>
      <div class="step-num">03</div><div class="step-label">Rewarding Loyalty</div>
    </div>
    <div class="step">
      <div class="step-ring"><svg viewBox="0 0 54 54" fill="#fff" stroke="#fff" stroke-width="3"><rect x="21" y="6" width="12" height="10"/><rect x="4" y="38" width="12" height="10"/><rect x="21" y="38" width="12" height="10"/><rect x="38" y="38" width="12" height="10"/><path d="M27 16v22M10 38v-8h34v8" fill="none"/></svg></div>
      <div class="step-num">04</div><div class="step-label">Collect Data</div>
    </div>
    <div class="step">
      <div class="step-ring"><svg viewBox="0 0 54 54" fill="none" stroke="#fff" stroke-width="3"><rect x="11" y="8" width="32" height="40" rx="2"/><rect x="20" y="4" width="14" height="7" fill="#fff"/><path d="M17 20h4M25 20h12M17 29h4M25 29h12M17 38h4M25 38h12"/></svg></div>
      <div class="step-num">05</div><div class="step-label">Data Analytics</div>
    </div>
  </div>
</section>

<section class="case">
  <h2 class="section-title heading">Case study</h2>
  <p class="case-sub">Results from a 31 day campaign</p>
  <div class="rule"></div>
  <div class="stats">
    <div class="stat"><div class="stat-value">650</div><div class="stat-label">VIP Card Holders</div></div>
    <div class="stat"><div class="stat-value">5000</div><div class="stat-label">Messages Sent</div></div>
    <div class="stat"><div class="stat-value">22%</div><div class="stat-label">Conversion Rate</div></div>
    <div class="stat"><div class="stat-value">1.2 Hours</div><div class="stat-label">AVG Dwell Time</div></div>
    <div class="stat"><div class="stat-value">95%</div><div class="stat-label">Holding Engagement</div></div>
    <div class="stat"><div class="stat-value">980</div><div class="stat-label">Loyalty Rewards Issued</div></div>
  </div>
</section>

<section class="closing" role="img" aria-label="Blue-tinted photo of a person working at a laptop">
  <p class="closing-text heading">Understanding your customers and identifying trends are key to a successful shopping centre, with our innovative and effective services Vostrelink can help you lead the way.</p>
</section>

<footer class="footer">
  <div class="footer-brand"><div class="brand-dot"></div><div class="brand-name">Vostrelink</div></div>
  <div class="footer-contact">
    <h4>CONTACT US</h4>
    <div class="contact-row"><svg viewBox="0 0 12 12" fill="#fff"><path d="M6 0a4 4 0 0 1 4 4c0 3-4 8-4 8S2 7 2 4a4 4 0 0 1 4-4z"/><circle cx="6" cy="4" r="1.5" fill="#333"/></svg><span>Unit 7b, Harbour Road<br>Kestrel, KT12 4RD</span></div>
    <div class="contact-row"><svg viewBox="0 0 12 12" fill="#fff"><path d="M2 1l2-1 2 3-1 1.5q1 2 2.5 2.5L9 6l3 2-1 2q-1 2-4 0Q2 7 1 3z"/></svg><span>02830 555 014</span></div>
    <div class="contact-row"><svg viewBox="0 0 12 12" fill="#fff"><rect x="0" y="2" width="12" height="8"/><path d="M0 2l6 5 6-5" fill="none" stroke="#333"/></svg><span>contact@vostrelink.com</span></div>
  </div>
  <div class="footer-menu">
    <h4>MENU</h4>
    What we do<br>Benefits<br>Testimonials<br>How it works<br>Case study<br>Contact
  </div>
  <div class="footer-news">
    <h4>NEWSLETTER</h4>
    <div class="news-input">E-mail id</div>
    <span class="news-btn">SIGNUP</span>
  </div>
  <div class="footer-line"></div>
  <div class="follow"><h4>FOLLOW US</h4><span class="social"></span><span class="social"></span><span class="social"></span></div>
  <div class="copyright">Copyrights @ 2018 All Rights Reserved</div>
</footer>

</body>
</html>
```